iPhone iOS 7 App For Managing Tasks/Photos for Internal Company Use

We need an app design that displays company objectives and task, and provides the interface for employees to complete a task by uploading a photo and adding comments.

Please see attached mock up sketches as a rough guideline

Final delivery of files must contain PSD, and all layers/objects sliced both is PSD and PNG files

Target Market(s)

This is a tool for internal employee use

Industry/Entity Type

It Company

Requirements
Must have
• Must include logo, and match the colour scheme
Use iPhone iOS 7 Style

```html
<!DOCTYPE html>
<html lang="en">
<head>
<meta charset="utf-8">
<title>Task Upload</title>
<link rel="stylesheet" href="https://fonts.googleapis.com/css2?family=Open+Sans:wght@600;700&family=Roboto:wght@300;400;500&display=swap">
<style>
  :root {
    --screen-bg: #a7bac5;
    --header-bg: #ffffff;
    --brand: #4d7b85;
    --brand-dot: #e8705a;
    --ring-track: #e3e7e8;
    --ring-progress: #ef6c4c;
    --ring-progress-light: #f48a68;
    --muted-text: #869aa2;
    --note-bg: #8fa5af;
    --note-border: #7e949e;
    --bar-bg: #f6f6f7;
    --field-border: #dcdde0;
    --action-blue: #1a7cf5;
    --icon-gray: #9a9a9e;
    --keyboard-bg: #d3d6db;
    --key-bg: #fdfdfd;
    --key-shadow: #8a8b8f;
    --key-special: #b4b9c1;
    --ink: #111;
  }
  * { box-sizing: border-box; margin: 0; padding: 0; }
  html, body { width: 675px; height: 1200px; overflow: hidden; }
  body {
    position: relative;
    background: var(--screen-bg);
    font-family: "Roboto", "Helvetica Neue", Arial, sans-serif;
    color: var(--ink);
  }

  /* Status bar */
  .status-bar {
    position: absolute; top: 0; left: 0; width: 675px; height: 51px;
    display: flex; align-items: center; justify-content: space-between;
    padding: 0 10px 0 12px; font-size: 23px; font-weight: 400;
  }
  .status-left, .status-right { display: flex; align-items: center; gap: 8px; }
  .status-time { position: absolute; left: 0; right: 0; text-align: center; font-weight: 500; pointer-events: none; }

  /* Header */
  .app-header {
    position: absolute; top: 51px; left: 0; width: 675px; height: 84px;
    background: var(--header-bg); z-index: 3;
    box-shadow: 0 2px 4px rgba(0,0,0,.12);
    display: flex; align-items: center; justify-content: center; gap: 14px;
  }
  .brand-dot { width: 26px; height: 26px; border-radius: 50%; background: var(--brand-dot); }
  .brand-name {
    font-family: "Open Sans", Arial, sans-serif; font-weight: 600;
    font-size: 32px; color: var(--brand); letter-spacing: .3px;
  }

  /* Upload progress */
  .upload-progress {
    position: absolute; left: 179px; top: 87px; width: 332px; height: 332px; z-index: 2;
  }
  .upload-label {
    position: absolute; left: 0; right: 0; top: 154px; text-align: center;
    font-family: "Open Sans", Arial, sans-serif; font-weight: 700;
    font-size: 22px; color: var(--muted-text);
  }
  .upload-icon { position: absolute; left: 134px; top: 92px; }

  /* Comment area */
  .comment-box {
    position: absolute; left: 95px; top: 424px; width: 524px; height: 209px;
    background: var(--note-bg); border: 1px solid var(--note-border);
  }
  .caret { position: absolute; left: 38px; top: 27px; width: 3px; height: 30px; background: #4b5d66; }

  /* Input bar */
  .input-bar {
    position: absolute; left: 0; top: 659px; width: 675px; height: 90px;
    background: var(--bar-bg); border-top: 1px solid #e2e3e6;
  }
  .camera-icon { position: absolute; left: 28px; top: 21px; }
  .label-field {
    position: absolute; left: 102px; top: 12px; width: 420px; height: 61px;
    background: #fff; border: 1px solid var(--field-border); border-radius: 8px;
    font-size: 25px; padding-left: 17px; line-height: 61px;
  }
  .send-action {
    position: absolute; left: 558px; top: 0; height: 90px; line-height: 90px;
    font-size: 34px; font-weight: 300; color: var(--action-blue);
  }

  /* Keyboard */
  .keyboard {
    position: absolute; left: 0; top: 749px; width: 675px; height: 451px;
    background: var(--keyboard-bg);
  }
  .key-row { position: absolute; left: 0; width: 675px; height: 78px; }
  .key {
    position: absolute; top: 0; height: 78px; width: 57px;
    background: var(--key-bg); border-radius: 8px;
    box-shadow: 0 2px 0 var(--key-shadow);
    display: flex; align-items: center; justify-content: center;
    font-size: 37px; font-weight: 300;
  }
  .key.special { background: var(--key-special); }
  .key.wide-label { font-size: 28px; }
</style>
</head>
<body>

<header class="status-bar">
  <div class="status-left">
    <svg width="86" height="16" viewBox="0 0 86 16" aria-hidden="true">
      <circle cx="8" cy="8" r="6.5" fill="#000"/><circle cx="25" cy="8" r="6.5" fill="#000"/><circle cx="42" cy="8" r="6.5" fill="#000"/>
      <circle cx="59" cy="8" r="6" fill="none" stroke="#000" stroke-width="1.3"/><circle cx="76" cy="8" r="6" fill="none" stroke="#000" stroke-width="1.3"/>
    </svg>
    <span>NOVA</span>
    <svg width="26" height="20" viewBox="0 0 26 20" aria-hidden="true">
      <path d="M13 19 L2 7 A16 16 0 0 1 24 7 Z" fill="#000"/>
    </svg>
  </div>
  <div class="status-time">4:21 PM</div>
  <div class="status-right">
    <svg width="16" height="24" viewBox="0 0 16 24" aria-hidden="true">
      <path d="M2 6 L13 17 L8 22 V2 L13 7 L2 18" fill="none" stroke="#333" stroke-width="1.8"/>
    </svg>
    <span>100%</span>
    <svg width="56" height="22" viewBox="0 0 56 22" aria-hidden="true">
      <rect x="1" y="1" width="49" height="20" rx="3" fill="none" stroke="#000" stroke-width="1.6"/>
      <rect x="4" y="4" width="43" height="14" rx="1.5" fill="#000"/>
      <rect x="51" y="7" width="3.5" height="8" rx="1" fill="#000"/>
    </svg>
  </div>
</header>

<div class="app-header">
  <span class="brand-dot"></span>
  <span class="brand-name">COMPANY NAME</span>
</div>

<div class="upload-progress">
  <svg width="332" height="332" viewBox="0 0 332 332" aria-hidden="true">
    <defs>
      <linearGradient id="progress-grad" x1="0" y1="0" x2="0" y2="1">
        <stop offset="0" stop-color="var(--ring-progress-light)"/>
        <stop offset="1" stop-color="var(--ring-progress)"/>
      </linearGradient>
      <filter id="soft-shadow" x="-20%" y="-20%" width="140%" height="140%">
        <feDropShadow dx="0" dy="3" stdDeviation="4" flood-opacity=".2"/>
      </filter>
    </defs>
    <circle cx="166" cy="166" r="162" fill="#fafbfb" filter="url(#soft-shadow)"/>
    <circle cx="166" cy="166" r="142" fill="none" stroke="var(--ring-track)" stroke-width="24"/>
    <circle cx="166" cy="166" r="142" fill="none" stroke="url(#progress-grad)" stroke-width="24"
            stroke-dasharray="455 1000" transform="rotate(-90 166 166)"/>
    <circle cx="166" cy="166" r="124" fill="#f7f8f8" filter="url(#soft-shadow)"/>
  </svg>
  <svg class="upload-icon" width="64" height="46" viewBox="0 0 64 46" aria-hidden="true">
    <path d="M16 44 A14 14 0 0 1 14 16 A19 19 0 0 1 50 14 A15 15 0 0 1 50 44 Z" fill="var(--ring-progress)"/>
    <path d="M32 38 V22 M25 28 L32 21 L39 28" fill="none" stroke="#fff" stroke-width="4" stroke-linecap="square"/>
  </svg>
  <div class="upload-label">Uploading Image</div>
</div>

<div class="comment-box"><span class="caret"></span></div>

<div class="input-bar">
  <svg class="camera-icon" width="52" height="44" viewBox="0 0 52 44" aria-hidden="true">
    <path d="M4 10 H14 L18 4 H34 L38 10 H48 A3 3 0 0 1 51 13 V41 A3 3 0 0 1 48 44 H4 A3 3 0 0 1 1 41 V13 A3 3 0 0 1 4 10 Z" fill="var(--icon-gray)"/>
    <circle cx="26" cy="26" r="11" fill="var(--bar-bg)"/>
    <circle cx="26" cy="26" r="8" fill="var(--icon-gray)"/>
    <rect x="5" y="6" width="6" height="3" fill="var(--icon-gray)"/>
  </svg>
  <div class="label-field">Label</div>
  <div class="send-action">Send</div>
</div>

<div class="keyboard">
  <div class="key-row" style="top:19px">
    <span class="key" style="left:6px">Q</span><span class="key" style="left:73px">W</span>
    <span class="key" style="left:141px">E</span><span class="key" style="left:208px">R</span>
    <span class="key" style="left:276px">T</span><span class="key" style="left:343px">Y</span>
    <span class="key" style="left:411px">U</span><span class="key" style="left:478px">I</span>
    <span class="key" style="left:546px">O</span><span class="key" style="left:612px">P</span>
  </div>
  <div class="key-row" style="top:133px">
    <span class="key" style="left:40px">A</span><span class="key" style="left:107px">S</span>
    <span class="key" style="left:175px">D</span><span class="key" style="left:242px">F</span>
    <span class="key" style="left:310px">G</span><span class="key" style="left:377px">H</span>
    <span class="key" style="left:445px">J</span><span class="key" style="left:512px">K</span>
    <span class="key" style="left:580px">L</span>
  </div>
  <div class="key-row" style="top:247px">
    <span class="key special" style="left:6px;width:76px">
      <svg width="32" height="30" viewBox="0 0 32 30" aria-hidden="true"><path d="M16 2 L30 16 H22 V28 H10 V16 H2 Z" fill="none" stroke="#333" stroke-width="1.8" stroke-linejoin="round"/></svg>
    </span>
    <span class="key" style="left:108px">Z</span><span class="key" style="left:175px">X</span>
    <span class="key" style="left:243px">C</span><span class="key" style="left:310px">V</span>
    <span class="key" style="left:378px">B</span><span class="key" style="left:445px">N</span>
    <span class="key" style="left:513px">M</span>
    <span class="key special" style="left:593px;width:76px">
      <svg width="40" height="28" viewBox="0 0 40 28" aria-hidden="true"><path d="M12 2 H37 V26 H12 L2 14 Z" fill="none" stroke="#333" stroke-width="1.8" stroke-linejoin="round"/><path d="M19 8 L30 20 M30 8 L19 20" stroke="#333" stroke-width="1.8"/></svg>
    </span>
  </div>
  <div class="key-row" style="top:361px">
    <span class="key special wide-label" style="left:6px;width:158px">123</span>
    <span class="key wide-label" style="left:176px;width:324px">space</span>
    <span class="key special wide-label" style="left:514px;width:155px">return</span>
  </div>
</div>

</body>
</html>
```